New, modern business card for growing audiology practice

We need a new business card for our audiology practice. Our logo and website have recently changed (more modern) and we want our business cards to reflect this change.
We conduct hearing tests, perform earwax removals, and fit & dispense hearing aids to our patients. We are a family owned practice in which the owner is the one who works directly with the patient. I have attached logos in various formats to use, as well as two ideas I found on this website; as well as a scanned copy of our current logo. Good luck!

Industry/Entity Type

Business

Contact Information for Business Card

Company name: Tolvera Hearing Center
Provider name: Peter Wolstenby, Au.D. F/NSB
Phone number: (440) 683-5127
Address: 837 W. Lindell Ave. Marrowby Falls, OH 44907
email: tolverahearing@postvane.com
website: tolverahearing.com

Colors
000000
aaaaaa
dbdbdb
cacaca
9bcb3c
afd23c
cadf82
b1b1b1

Requirements
Must have
• My card must include information in the "details" section. In the attached images, I found a few that I liked and I would like to model after - "brisky bouncin'" and "Sound Method Center".
• Must be horizontal.
• Must include logos provided. I uploaded them in various file formats and various ways.
• Must match logo font, if possible, if not, please get as close as you can.
Nice to have
• I really like the idea of having a color on one side with just the logo and company name and the contact information and provider name on the other side. I also really like the idea of having the main color dominating on the logo/company side with accent of that same color on the contact side of the card.
Should not have
• Must not be vertical.

```html
<!DOCTYPE html>
<html lang="en">
<head>
<meta charset="utf-8">
<title>Tolvera Hearing Center – Business Card</title>
<link rel="stylesheet" href="https://fonts.googleapis.com/css2?family=Montserrat:wght@300;400;500&display=swap">
<style>
  :root {
    --brand-green: #7ba843;
    --brand-green-soft: #bcd6a0;
    --ink: #111111;
    --paper: #ffffff;
    --backdrop: #e4e4e4;
    --card-w: 700px;
    --card-h: 400px;
  }
  * { box-sizing: border-box; margin: 0; padding: 0; }
  html, body {
    width: 1200px; height: 900px; overflow: hidden;
    background: var(--backdrop);
    font-family: "Montserrat", sans-serif;
  }
  .sheet {
    width: 1200px; height: 900px;
    display: flex; flex-direction: column; align-items: center; justify-content: center;
    gap: 34px;
  }
  .card {
    position: relative;
    width: var(--card-w); height: var(--card-h);
    overflow: hidden;
    box-shadow: 0 6px 18px rgba(0,0,0,.18);
  }

  /* Front side */
  .card--front {
    background: var(--brand-green);
    display: flex; align-items: center; justify-content: center;
  }
  .front-mark {
    display: flex; align-items: center; gap: 18px;
    color: var(--paper);
    font-weight: 500; font-size: 30px; letter-spacing: 0.5px;
    text-transform: uppercase;
  }
  .front-mark__dot {
    width: 46px; height: 46px; border-radius: 50%;
    background: var(--paper);
  }

  /* Back side */
  .card--back { background: var(--paper); }
  .back-strip {
    position: absolute; left: 0; top: 0; bottom: 0; width: 92px;
    background: var(--brand-green);
  }
  .back-accent {
    position: absolute; right: -70px; top: 40px;
    width: 210px; height: 210px; border-radius: 50%;
    background: var(--brand-green-soft);
  }
  .back-content {
    position: absolute; left: 128px; top: 78px;
    color: var(--ink);
  }
  .brand-line {
    display: flex; align-items: center; gap: 10px;
    font-weight: 500; font-size: 22px; letter-spacing: 0.3px;
    text-transform: uppercase;
  }
  .brand-line__dot {
    width: 18px; height: 18px; border-radius: 50%;
    background: var(--brand-green);
  }
  .provider { margin-top: 30px; }
  .provider__name {
    color: var(--brand-green);
    font-weight: 300; font-size: 27px; letter-spacing: 0.5px;
    text-transform: uppercase;
  }
  .provider__title { font-size: 16px; margin-top: 2px; }
  .contact-list { list-style: none; margin-top: 22px; font-size: 16px; line-height: 1.5; }
  .contact-list li { display: flex; align-items: center; gap: 10px; }
  .contact-list svg { width: 14px; height: 14px; fill: var(--brand-green); flex: none; }
  .address { margin-top: 26px; font-size: 17px; line-height: 1.35; font-style: normal; }
</style>
</head>
<body>
<main class="sheet">

  <section class="card card--front" aria-label="Card front">
    <div class="front-mark">
      <span class="front-mark__dot"></span>
      <span>Tolvera Hearing Center</span>
    </div>
  </section>

  <section class="card card--back" aria-label="Card back">
    <div class="back-strip"></div>
    <div class="back-accent"></div>
    <div class="back-content">
      <div class="brand-line">
        <span class="brand-line__dot"></span>
        <span>Tolvera Hearing Center</span>
      </div>

      <div class="provider">
        <div class="provider__name">Peter Wolstenby</div>
        <div class="provider__title">Au.D. F/NSB</div>
      </div>

      <ul class="contact-list">
        <li>
          <svg viewBox="0 0 24 24" aria-hidden="true"><path d="M6.6 10.8a15.2 15.2 0 0 0 6.6 6.6l2.2-2.2c.3-.3.7-.4 1-.2 1.1.4 2.3.6 3.6.6.6 0 1 .4 1 1V20c0 .6-.4 1-1 1A17 17 0 0 1 3 4c0-.6.4-1 1-1h3.5c.6 0 1 .4 1 1 0 1.3.2 2.5.6 3.6.1.3 0 .7-.2 1z"/></svg>
          (440) 683-5127
        </li>
        <li>
          <svg viewBox="0 0 24 24" aria-hidden="true"><path d="M2 5h20v14H2z M3.5 6.5 12 13l8.5-6.5" stroke="#fff" stroke-width="1.4"/></svg>
          tolverahearing@postvane.com
        </li>
        <li>
          <svg viewBox="0 0 24 24" aria-hidden="true"><path d="M12 2a10 10 0 1 0 0 20 10 10 0 0 0 0-20zm0 2c1 1.3 1.8 3.3 2 6H10c.2-2.7 1-4.7 2-6zM4.1 11H8c.1 2 .5 3.9 1.2 5.4A8 8 0 0 1 4.1 11zm0-2a8 8 0 0 1 5.1-5.4C8.5 5.1 8.1 7 8 9zM12 20c-1-1.3-1.8-3.3-2-6h4c-.2 2.7-1 4.7-2 6zm2.8-3.6c.7-1.5 1.1-3.4 1.2-5.4h3.9a8 8 0 0 1-5.1 5.4zM16 9c-.1-2-.5-3.9-1.2-5.4A8 8 0 0 1 19.9 9z"/></svg>
          www.tolverahearing.com
        </li>
      </ul>

      <address class="address">
        837 W. Lindell Ave.<br>
        Marrowby Falls, OH 44907
      </address>
    </div>
  </section>

</main>
</body>
</html>
```